Velvet Riot Rising Line of Sparkling Wine & Spirits

Back info: Nora Beth Quill Owner 555-318-4402 1480 E. Harlow Ave, Bldg. 2, & 3, Marlow Ca. 95871
Sparkling Wines & Memorabilia www.velvetriotrising.com
Ok I have uploaded the winning design. The color that I am after is the Fushia, Raspberry, Red, Matte Satin Matalic Finish. With a 24 Karet Gold color Foil. The Bottle is on the top row and it's the 2nd Bottle in. That is the Color that I want. This is the style of font. Make sure that you put what we're advertising. Good Luck to you all. Warmest regards, Nora
21 & up UniSex
Sparkling Wine and Memorabilia
there listed up above.....

```html
<!DOCTYPE html>
<html lang="en">
<head>
<meta charset="utf-8">
<title>Velvet Riot Rising – Business Card</title>
<link href="https://fonts.googleapis.com/css2?family=Cinzel:wght@600;700&family=Great+Vibes&family=Poppins:wght@400;600&display=swap" rel="stylesheet">
<style>
  :root {
    --backdrop: #9c9c9c;
    --card-black: #1a1a1a;
    --fuchsia-deep: #b80f5e;
    --fuchsia-bright: #e2198f;
    --ornament-pink: #f21fa6;
    --ornament-black: #0b0608;
    --gold: #c8903f;
    --gold-light: #d29a52;
    --ink: #120a0e;
  }
  * { margin: 0; padding: 0; box-sizing: border-box; }
  html, body { width: 1200px; height: 1000px; overflow: hidden; }
  body {
    background: var(--backdrop);
    position: relative;
    font-family: "Poppins", sans-serif;
  }
  .card {
    position: absolute;
    width: 543px;
    height: 312px;
    border-radius: 24px;
    overflow: hidden;
  }
  .card--front {
    left: 37px;
    top: 330px;
    background: var(--card-black);
  }
  .card--back {
    left: 618px;
    top: 334px;
    height: 313px;
    background: linear-gradient(100deg, var(--fuchsia-deep) 0%, var(--fuchsia-bright) 55%, var(--ornament-pink) 100%);
  }
  .brand-name {
    font-family: "Cinzel", serif;
    font-weight: 700;
    color: var(--gold);
    white-space: nowrap;
    line-height: 1;
  }
  .brand-tagline {
    font-family: "Cinzel", serif;
    font-weight: 600;
    color: var(--gold-light);
    white-space: nowrap;
    text-transform: uppercase;
    line-height: 1;
  }
  .front-lockup {
    position: absolute;
    left: 0;
    width: 100%;
    top: 128px;
    display: flex;
    flex-direction: column;
    align-items: center;
  }
  .card--front .brand-name { font-size: 31px; letter-spacing: 0.5px; }
  .card--front .brand-tagline { font-size: 10.5px; letter-spacing: 4px; margin-top: 24px; }

  .contact-block {
    position: absolute;
    left: 0;
    top: 0;
    width: 292px;
    height: 100%;
    color: var(--ink);
    text-align: center;
  }
  .contact-block > * {
    position: absolute;
    left: 0;
    width: 100%;
    display: flex;
    justify-content: center;
  }
  .card--back .brand-name { top: 48px; font-size: 19px; letter-spacing: 0.3px; }
  .card--back .brand-tagline { top: 92px; font-size: 7px; letter-spacing: 2.4px; color: var(--gold); }
  .owner-name {
    top: 118px;
    font-family: "Great Vibes", cursive;
    font-size: 32px;
    line-height: 1;
  }
  .owner-title {
    top: 160px;
    font-family: "Cinzel", serif;
    font-weight: 700;
    font-size: 13px;
    letter-spacing: 3px;
    line-height: 1;
  }
  .contact-lines {
    top: 181px;
    list-style: none;
    flex-direction: column;
    align-items: center;
    font-size: 11.6px;
    line-height: 16px;
  }
  .social-marks { top: 254px; gap: 5px; }
  .social-marks span {
    width: 14px; height: 14px; border-radius: 50%;
    background: var(--ink);
  }
  .website { top: 272px; font-size: 12.5px; line-height: 16px; }
  .website strong { font-weight: 600; }

  .ornament-panel {
    position: absolute;
    right: 0;
    top: 0;
    width: 290px;
    height: 100%;
    background: radial-gradient(ellipse 78% 95% at 78% 50%, var(--ornament-black) 0%, var(--ornament-black) 55%, rgba(58,10,38,0.75) 78%, rgba(242,31,166,0) 100%);
  }
</style>
</head>
<body>
  <section class="card card--front" aria-label="Card front">
    <div class="front-lockup">
      <h1 class="brand-name">Velvet Riot Rising</h1>
      <p class="brand-tagline">Line of Sparkling Wine &amp; Spirits</p>
    </div>
  </section>

  <section class="card card--back" aria-label="Card back">
    <div class="ornament-panel" role="img" aria-label="Ornate black baroque scrollwork framing a crest shield"></div>
    <div class="contact-block">
      <h2 class="brand-name">Velvet Riot Rising</h2>
      <p class="brand-tagline">Line of Sparkling Wine &amp; Spirits</p>
      <p class="owner-name">Nora Beth Quill</p>
      <p class="owner-title">OWNER</p>
      <ul class="contact-lines">
        <li>(555) 318-4402</li>
        <li>nora@velvetriotrising.com</li>
        <li>1480 E. Harlow Ave, Bldg. 2, &amp; 3</li>
        <li>Marlow Ca. 95871</li>
      </ul>
      <div class="social-marks" aria-hidden="true"><span></span><span></span></div>
      <p class="website"><strong>velvetriotrising</strong>.com</p>
    </div>
  </section>
</body>
</html>
```